Business Cards - Brightpath Horizon

need to design unique business card for my mortgage business. I need to design credit card style business card for my business or any unique idea that you might have

Target Market(s)

Home Loan customers

Industry/Entity Type

Mortgage Brokerage

Contact Information for Business Card

please design credit card style or very unique style business card

Colors

Designer to choose colors to be used in the design.

Requirements
Must have
• Name
• position
• Phone number
• fax number
• email address
• website address
• social media address
• All above fields will be provided once design in finalised

```html
<!DOCTYPE html>
<html lang="en">
<head>
<meta charset="utf-8">
<title>Brightpath Horizon – Business Cards</title>
<link rel="stylesheet" href="https://fonts.googleapis.com/css2?family=Libre+Baskerville:wght@400&family=Roboto:wght@400;500&display=swap">
<style>
  :root {
    --backdrop: #1b1b1d;
    --brand-blue: #2f479e;
    --brand-blue-light: #3d56ad;
    --brand-blue-deep: #233a8c;
    --accent-orange: #e27a1c;
    --card-white: #ffffff;
    --mist: rgba(214, 232, 244, 0.6);
    --ink-light: #f2f4fb;
  }
  * { margin: 0; padding: 0; box-sizing: border-box; }
  html, body { width: 1200px; height: 963px; overflow: hidden; background: var(--backdrop); }
  .sheet { position: relative; width: 1200px; height: 963px; }

  .card {
    position: absolute;
    left: 250px;
    width: 700px;
    height: 400px;
    border-radius: 22px;
    overflow: hidden;
  }

  /* Front */
  .card--front { top: 48px; background: var(--card-white); }
  .front-band {
    position: absolute; left: 0; right: 0; bottom: 0; height: 160px;
    background: var(--brand-blue);
  }
  .front-mist {
    position: absolute; right: 80px; top: 96px; width: 200px; height: 140px;
    border-radius: 50% 50% 10% 10%;
    background: radial-gradient(ellipse at 50% 45%, var(--mist), rgba(214,232,244,0.2) 70%, rgba(214,232,244,0) 100%);
  }
  .brand {
    position: absolute; left: 48px; top: 46px;
    display: flex; align-items: center; gap: 14px;
  }
  .brand-square { width: 18px; height: 18px; background: var(--accent-orange); }
  .brand-name {
    font-family: "Libre Baskerville", Georgia, serif;
    font-size: 34px; color: var(--brand-blue); letter-spacing: 1px;
  }
  .person { position: absolute; left: 48px; top: 134px; }
  .person-name {
    font-family: "Libre Baskerville", Georgia, serif;
    font-size: 22px; color: var(--brand-blue); letter-spacing: 1.5px;
  }
  .person-role {
    font-family: "Roboto", Arial, sans-serif; font-size: 15px;
    color: var(--accent-orange); margin-top: 4px;
  }
  .name-rule {
    position: absolute; left: 150px; right: 48px; top: 200px;
    height: 1.5px; background: var(--brand-blue);
  }
  .contacts {
    position: absolute; left: 48px; top: 266px; list-style: none;
    font-family: "Roboto", Arial, sans-serif; font-size: 15px; color: var(--ink-light);
  }
  .contacts li { display: flex; align-items: center; gap: 10px; margin-bottom: 8px; }
  .contacts svg { width: 13px; height: 13px; fill: none; stroke: var(--ink-light); stroke-width: 1.6; }
  .address {
    position: absolute; right: 48px; bottom: 36px; text-align: right;
    font-family: "Roboto", Arial, sans-serif; font-size: 16px; line-height: 1.45;
    color: var(--ink-light);
  }

  /* Back */
  .card--back {
    top: 512px;
    background: linear-gradient(135deg, var(--brand-blue-deep), var(--brand-blue-light) 55%, var(--brand-blue));
  }
  .back-brand {
    position: absolute; left: 0; right: 0; top: 150px;
    display: flex; justify-content: center; align-items: center; gap: 16px;
  }
  .back-brand .brand-name { color: var(--ink-light); font-size: 42px; }
  .back-web {
    position: absolute; left: 0; right: 0; bottom: 70px; text-align: center;
    font-family: "Roboto", Arial, sans-serif; font-size: 17px; letter-spacing: 1.5px;
    color: var(--ink-light);
  }
</style>
</head>
<body>
<main class="sheet">

  <section class="card card--front" aria-label="Business card front">
    <div class="front-band"></div>
    <div class="front-mist" role="img" aria-label="Faint tree silhouette decoration"></div>

    <div class="brand">
      <span class="brand-name">Brightpath Horizon</span>
      <span class="brand-square"></span>
    </div>

    <div class="person">
      <p class="person-name">DANIEL CARTER</p>
      <p class="person-role">Founder</p>
    </div>
    <div class="name-rule"></div>

    <ul class="contacts">
      <li>
        <svg viewBox="0 0 16 16"><path d="M4 1.5l2.5 3-1.6 1.6a9 9 0 0 0 5 5l1.6-1.6 3 2.5-1.8 2.2C7.5 14 2 8.5 1.8 3.3z"/></svg>
        555-014-2368
      </li>
      <li>
        <svg viewBox="0 0 16 16"><rect x="1.5" y="3.5" width="13" height="9"/><path d="M1.5 3.5l6.5 5 6.5-5"/></svg>
        hello@brightpathmail.com
      </li>
      <li>
        <svg viewBox="0 0 16 16"><circle cx="8" cy="8" r="6.5"/><path d="M1.5 8h13M8 1.5c-3 3.5-3 9.5 0 13M8 1.5c3 3.5 3 9.5 0 13"/></svg>
        www.brightpathloans.com
      </li>
    </ul>

    <p class="address">48 Harbor View Ln.<br>Coral Bay, FL 30215</p>
  </section>

  <section class="card card--back" aria-label="Business card back">
    <div class="back-brand">
      <span class="brand-name">Brightpath Horizon</span>
      <span class="brand-square"></span>
    </div>
    <p class="back-web">www.yourwebsite.com</p>
  </section>

</main>
</body>
</html>
```